Webshop Template

For our Webstore in UK we need a complete Template,
shoppingcart is Magento, the Shop is focussed on Download software,

the name: Kelvoramarket.co.uk

Check out some other good stores, like zandrilo.de
Updates

for example the Page from 

www.brunt.co.uk or

www.zandrilo.de

www.mokvelta.de

www.quarnepreis.de

The Logodesign which are in Consideration

http://www.plimvector.com/design/5520913/logo-design-by-tomek7ga

http://www.plimvector.com/design/5518207/logo-design-by-ivanoralba

http://www.plimvector.com/design/5517346/logo-design-by-granite-fables

http://www.plimvector.com/design/5516085/logo-design-by-quillotaste

http://www.plimvector.com/design/5515472/logo-design-by-tuvaro

http://www.plimvector.com/design/5514619/logo-design-by-lone-pine-graphic-

Target Market(s)

B2C - Consumer Marcet

Industry/Entity Type

Shop

```html
<!DOCTYPE html>
<html lang="en">
<head>
<meta charset="utf-8">
<title>Kelvoramarket – Download Software Store</title>
<link rel="stylesheet" href="https://fonts.googleapis.com/css2?family=Crimson+Text:wght@400&family=Open+Sans:ital,wght@0,400;0,600;1,600;1,700&display=swap">
<style>
:root{
  --red:#e60000;
  --red-dark:#a80000;
  --black:#000;
  --ink:#222;
  --grey:#888;
  --light:#ccc;
  --footer-base:#111;
  --white:#fff;
}
*{box-sizing:border-box;margin:0;padding:0}
html,body{width:1200px;height:1200px;overflow:hidden;background:var(--white)}
body{position:relative;font-family:"Open Sans",Arial,sans-serif;color:var(--ink)}
.abs{position:absolute}
.top-band{left:0;top:0;width:1200px;height:7px;background:var(--black)}
.account-tab{left:745px;top:7px}
.account-links{left:788px;top:10px;font-family:"Crimson Text",Georgia,serif;font-size:15px;color:var(--white);white-space:nowrap}
.account-links span.sep{margin:0 6px;opacity:.8}
.brand{left:134px;top:34px;font-family:"Crimson Text",Georgia,serif;font-size:31px;color:var(--red);letter-spacing:.3px}
.search{left:732px;top:71px;width:164px;height:30px;border:1px solid var(--light);border-bottom:none;border-radius:8px 8px 0 0;padding:6px 14px;font-family:"Crimson Text",Georgia,serif;font-size:15px;color:var(--grey)}
.search svg{position:absolute;right:8px;top:7px}
.auth{left:901px;top:71px;width:189px;height:30px;background:var(--red);border-radius:8px 8px 0 0;color:var(--white);font-family:"Crimson Text",Georgia,serif;font-size:15px;display:flex;align-items:center;justify-content:center;gap:22px}
.main-nav{left:109px;top:100px;width:981px;height:49px;background:linear-gradient(#1b1b1b,#000 55%);border-radius:8px;font-family:"Crimson Text",Georgia,serif;font-size:19px;color:var(--white)}
.main-nav span{position:absolute;top:12px;white-space:nowrap}
.main-nav .current{color:#ff1a1a}
.hero{left:111px;top:150px;width:725px;height:349px;background:radial-gradient(circle at 60% 40%,#ef0a0a,#d40000 70%);border-radius:8px}
.hero-title{left:147px;top:244px;width:330px;font-size:26px;line-height:36px;color:var(--white)}
.download{left:147px;top:377px;width:201px;height:46px;border-radius:9px;background:linear-gradient(#fff,#d7d7d7);box-shadow:0 2px 3px rgba(0,0,0,.35);font-style:italic;font-weight:600;font-size:20px;color:#222;padding:8px 13px}
.download i{position:absolute;right:8px;top:5px;width:34px;height:34px;border-radius:50%;background:linear-gradient(#d0d0d0,#a0a0a0)}
.download i:after{content:"";position:absolute;left:9px;top:13px;border:8px solid transparent;border-top:11px solid #111;border-bottom:none}
.dot{top:465px;width:13px;height:13px;border-radius:50%;background:#8d0000}
.dot.on{background:var(--white)}
.hero-visual{left:480px;top:160px;width:268px;height:330px;border-radius:14px;background:linear-gradient(160deg,#2a2f3a 0%,#3b4a6b 40%,#c9c9c9 80%,#9a9a9a 100%)}
.brand-strip{left:111px;top:490px;width:725px;height:85px;background:var(--black);border-radius:0 0 8px 8px;z-index:-1}
.partners{left:111px;top:525px;width:725px;display:flex;justify-content:space-around;font-size:18px;font-weight:600;color:#8a8a8a}
.side-menu{left:840px;top:150px;width:247px;height:611px;background:var(--red);border-radius:8px}
.side-menu li{position:absolute;left:47px;list-style:none;font-size:13px;color:var(--white);white-space:nowrap}
.side-menu li:before{content:"";position:absolute;left:-28px;top:6px;width:6px;height:6px;border-radius:50%;background:var(--black);box-shadow:12px 0 0 var(--white)}
.section-title{left:113px;top:583px;font-style:italic;font-weight:600;font-size:20px;color:#111;letter-spacing:-.3px}
.card{top:614px;width:137px;height:147px;border:1px solid #c9c9c9;border-radius:6px;background:var(--white)}
.card .shot{position:absolute;left:12px;top:28px;width:111px;height:90px;border-radius:4px}
.card-text{top:770px;width:136px}
.card-text h3{font-style:italic;font-weight:700;font-size:12.5px;color:#111;letter-spacing:-.2px}
.card-text p{margin-top:4px;font-size:11px;line-height:14px;text-align:justify;color:#333;letter-spacing:-.2px}
.detail{top:843px;width:74px;height:25px;border-radius:13px;background:linear-gradient(#555,#222);box-shadow:0 2px 2px rgba(0,0,0,.4);color:var(--white);font-style:italic;font-weight:600;font-size:13px;text-align:center;line-height:25px}
.footer{left:0;top:885px;width:1200px;height:250px;background:var(--black)}
.footer-base{left:0;top:1135px;width:1200px;height:65px;background:var(--footer-base)}
.foot-title{top:911px;font-style:italic;font-weight:600;font-size:20px;color:var(--white);letter-spacing:-.3px}
.demo{left:121px;top:954px;width:233px;height:151px;border:3px solid var(--white);background:linear-gradient(135deg,#6a6a6a,#3b3b3b 55%,#8a7f78)}
.play{left:216px;top:1008px}
.mail-input{left:423px;top:964px;width:209px;height:35px;background:var(--white);border:1px solid #ddd;font-family:Arial,sans-serif;font-size:11px;color:#333;padding:10px 11px}
.mail-input svg{position:absolute;right:10px;top:8px}
.hint{left:423px;top:1008px;width:190px;font-size:11px;line-height:14px;color:#555}
.subscribe{left:559px;top:1046px;width:73px;height:24px;border-radius:12px;background:linear-gradient(#555,#222);color:var(--white);font-style:italic;font-weight:600;font-size:13px;text-align:center;line-height:24px}
.links{top:951px;list-style:none;font-family:Arial,sans-serif;font-size:12px;line-height:18px;color:var(--light)}
.copyright{left:125px;top:1152px;font-family:Arial,sans-serif;font-size:12px;color:var(--light);word-spacing:3px}
.social{left:920px;top:1155px}
</style>
</head>
<body>
<div class="abs top-band"></div>
<svg class="abs account-tab" width="360" height="31" viewBox="0 0 360 31" aria-hidden="true"><path d="M0 0H360L346 24Q342 31 334 31H22Q14 31 11 24Z" fill="#e60000"/></svg>
<div class="abs account-links">My Account<span class="sep">|</span>My Cart<span class="sep">|</span>Checkout<span class="sep">|</span>Help</div>

<div class="abs brand">Kelvoramarket</div>

<div class="abs search">Search
  <svg width="18" height="18" viewBox="0 0 18 18" aria-hidden="true"><circle cx="10" cy="7" r="5.5" fill="none" stroke="#777" stroke-width="2"/><path d="M6 11L1.5 16" stroke="#777" stroke-width="3" stroke-linecap="round"/></svg>
</div>
<div class="abs auth"><span>Register</span><span>|</span><span>Login</span></div>

<nav class="abs main-nav">
  <span class="current" style="left:63px">Home</span>
  <span style="left:143px">About Us</span>
  <span style="left:243px">Software</span>
  <span style="left:342px">For PC</span>
  <span style="left:433px">Products</span>
  <span style="left:530px">Services</span>
  <span style="left:625px">Categories</span>
  <span style="left:739px">Mobile</span>
  <span style="left:817px">Tabio</span>
  <span style="left:888px">Fonique</span>
</nav>

<section class="abs hero"></section>
<h1 class="abs hero-title" style="font-weight:400">Lorem Ipsum is simply dummy text of the printing and typesetting industry.</h1>
<div class="abs download">Download Now<i></i></div>
<div class="abs dot" style="left:134px"></div>
<div class="abs dot" style="left:155px"></div>
<div class="abs dot" style="left:176px"></div>
<div class="abs dot on" style="left:197px"></div>
<div class="abs hero-visual" role="img" aria-label="Desktop computer showing a website on screen"></div>

<div class="abs brand-strip"></div>
<div class="abs partners"><span>Varnel</span><span>Orchana</span><span>Tuvio</span><span>Kestro</span><span>Hexli</span><span>Quintra</span><span>Lomeva</span><span>Pravion</span></div>

<ul class="abs side-menu">
  <li style="top:28px">Software</li>
  <li style="top:64px">Nuvo Games</li>
  <li style="top:100px">Plexa Games</li>
  <li style="top:136px">Korvix Games</li>
  <li style="top:172px">Duora Games</li>
  <li style="top:208px">PC Games</li>
  <li style="top:244px">PC Software</li>
  <li style="top:280px">Word Software</li>
  <li style="top:316px">Antivirus</li>
  <li style="top:352px">Lumvane Software</li>
  <li style="top:388px">Accounts Software</li>
  <li style="top:424px">Sorvel Software</li>
  <li style="top:460px">Trelix Software</li>
  <li style="top:496px">Orchana Software</li>
  <li style="top:532px">Fonique Games</li>
  <li style="top:568px">Mobile Phone Games</li>
</ul>

<h2 class="abs section-title">Featured Products</h2>

<div class="abs card" style="left:112px"><div class="shot" role="img" aria-label="Flat screen television" style="background:linear-gradient(#1f6fa8,#5fb8d8 60%,#222)"></div></div>
<div class="abs card" style="left:259px"><div class="shot" role="img" aria-label="Black laptop" style="background:linear-gradient(135deg,#555,#1a1a1a 60%,#bbb)"></div></div>
<div class="abs card" style="left:406px"><div class="shot" role="img" aria-label="Smartphone and tablet bundle" style="background:linear-gradient(135deg,#222,#444 55%,#d33 85%,#eee)"></div></div>
<div class="abs card" style="left:553px"><div class="shot" role="img" aria-label="Convertible laptop" style="background:linear-gradient(135deg,#2a3f8f,#6a2f8a 45%,#222 70%,#e07020)"></div></div>
<div class="abs card" style="left:700px"><div class="shot" role="img" aria-label="All-in-one desktop computers" style="background:linear-gradient(135deg,#4f8a3a,#c9c9c9 45%,#e03a6a 70%,#f2a020)"></div></div>

<div class="abs card-text" style="left:115px"><h3>Software Name</h3><p>Lorem Ipsum is simply dummy text of the printing and typesetting industry.</p></div>
<div class="abs card-text" style="left:261px"><h3>Software Name</h3><p>Lorem Ipsum is simply dummy text of the printing and typesetting industry.</p></div>
<div class="abs card-text" style="left:407px"><h3>Software Name</h3><p>Lorem Ipsum is simply dummy text of the printing and typesetting industry.</p></div>
<div class="abs card-text" style="left:554px"><h3>Software Name</h3><p>Lorem Ipsum is simply dummy text of the printing and typesetting industry.</p></div>
<div class="abs card-text" style="left:701px"><h3>Software Name</h3><p>Lorem Ipsum is simply dummy text of the printing and typesetting industry.</p></div>

<div class="abs detail" style="left:114px">Detail</div>
<div class="abs detail" style="left:261px">Detail</div>
<div class="abs detail" style="left:406px">Detail</div>
<div class="abs detail" style="left:554px">Detail</div>
<div class="abs detail" style="left:700px">Detail</div>

<footer class="abs footer"></footer>
<div class="abs footer-base"></div>

<h2 class="abs foot-title" style="left:119px">Latest Demo</h2>
<h2 class="abs foot-title" style="left:422px">Newsletter</h2>
<h2 class="abs foot-title" style="left:695px">Services</h2>
<h2 class="abs foot-title" style="left:887px">Softwares</h2>

<div class="abs demo" role="img" aria-label="Hand holding a smartphone, demo video still"></div>
<svg class="abs play" width="42" height="42" viewBox="0 0 42 42" aria-hidden="true"><circle cx="21" cy="21" r="19" fill="#fff" stroke="#222" stroke-width="3"/><circle cx="21" cy="21" r="14" fill="#333"/><path d="M16 13L29 21L16 29Z" fill="#fff"/></svg>

<div class="abs mail-input">Enter your mail ID
  <svg width="30" height="20" viewBox="0 0 30 20" aria-hidden="true"><rect x="1" y="1" width="28" height="18" fill="#eef3f6" stroke="#8aa" stroke-width="1"/><path d="M1 1L15 12L29 1" fill="none" stroke="#8aa"/></svg>
</div>
<p class="abs hint">Here type your id and subscribe a newsletter</p>
<div class="abs subscribe">Subscribe</div>

<ul class="abs links" style="left:694px"><li>Consectetur</li><li>Mauris ideaui</li><li>Aunc vivera ornare</li><li>Nunc convallis</li><li>Nulla faucibusodio</li></ul>
<ul class="abs links" style="left:887px"><li>Consectetur</li><li>Mauris ideaui</li><li>Aunc vivera ornare</li><li>Nunc convallis</li><li>Nulla faucibusodio</li></ul>

<p class="abs copyright">Copyright &nbsp;© &nbsp;2013 &nbsp;www.kelvoramarket.co.uk &nbsp;All rights reserved.</p>

<svg class="abs social" width="126" height="26" viewBox="0 0 126 26" aria-hidden="true">
  <circle cx="12" cy="12" r="12" fill="#666"/>
  <circle cx="46" cy="12" r="12" fill="#666"/>
  <circle cx="79" cy="12" r="12" fill="#666"/>
  <circle cx="113" cy="12" r="12" fill="#666"/>
  <rect x="105" y="6.5" width="16" height="11" fill="none" stroke="#222" stroke-width="1.6"/>
  <path d="M105 6.5L113 13L121 6.5" fill="none" stroke="#222" stroke-width="1.6"/>
</svg>
</body>
</html>
```